Harborline Auto LLC

Car Dealer Customer Service
Address: 2874 Cresthaven Road, Shelbyville, TN 37162
web: www.harborlineautoxq.net
email: harborlineautoxq@mailnest.example
Phone: (931) 555-0148
Phone: (629) 555-0173

```html
<!DOCTYPE html>
<html lang="en">
<head>
<meta charset="utf-8">
<title>Harborline Auto – Business Card</title>
<link rel="stylesheet" href="https://fonts.googleapis.com/css2?family=Montserrat:wght@400;500;800&display=swap">
<style>
  :root {
    --bg: #e9eaec;
    --paper: #ffffff;
    --brand-blue: #1f7aaf;
    --accent-gold: #ecb23c;
    --ink-light: #ffffff;
  }
  * { box-sizing: border-box; margin: 0; padding: 0; }
  html, body {
    width: 1200px; height: 900px; overflow: hidden;
    background: var(--bg);
    font-family: "Montserrat", sans-serif;
  }
  .sheet {
    position: relative; width: 1200px; height: 900px;
  }
  .card {
    position: absolute; left: 250px; width: 700px; height: 400px;
    background: var(--paper);
    box-shadow: 0 6px 18px rgba(0,0,0,0.12);
    overflow: hidden;
  }
  .card--front { top: 40px; }
  .card--back { top: 460px; }

  .brand {
    position: absolute; display: flex; align-items: center; gap: 16px;
  }
  .brand__dot {
    border-radius: 50%; background: var(--brand-blue); flex: none;
  }
  .brand__name {
    color: var(--brand-blue); font-weight: 800; text-transform: uppercase;
    letter-spacing: 1px; white-space: nowrap;
  }
  .card--front .brand { left: 50%; top: 50%; transform: translate(-50%, -50%); }
  .card--front .brand__dot { width: 64px; height: 64px; }
  .card--front .brand__name { font-size: 40px; }

  .card__backdrop { position: absolute; inset: 0; }
  .card--back .brand { right: 40px; top: 110px; gap: 12px; }
  .card--back .brand__dot { width: 40px; height: 40px; }
  .card--back .brand__name { font-size: 23px; }

  .contact {
    position: absolute; left: 44px; bottom: 40px;
    color: var(--ink-light); font-size: 16px; line-height: 1.5; font-weight: 400;
  }
  .contact__address { margin-bottom: 14px; }
  .contact__list { list-style: none; }
  .contact__item { display: flex; align-items: center; gap: 12px; }
  .contact__icon { width: 16px; height: 16px; flex: none; }
</style>
</head>
<body>
<main class="sheet">
  <section class="card card--front" aria-label="Card front">
    <div class="brand">
      <span class="brand__dot"></span>
      <span class="brand__name">Harborline Auto</span>
    </div>
  </section>

  <section class="card card--back" aria-label="Card back">
    <svg class="card__backdrop" viewBox="0 0 700 400" preserveAspectRatio="none" aria-hidden="true">
      <rect width="700" height="400" fill="var(--brand-blue)"/>
      <path d="M300 0 Q340 320 700 350 L700 0 Z" fill="var(--accent-gold)"/>
      <path d="M322 0 Q365 300 700 330 L700 0 Z" fill="var(--paper)"/>
    </svg>

    <div class="brand">
      <span class="brand__dot"></span>
      <span class="brand__name">Harborline Auto</span>
    </div>

    <div class="contact">
      <p class="contact__address">Car Dealer Customer Service<br>2874 Cresthaven Road<br>Shelbyville, TN 37162</p>
      <ul class="contact__list">
        <li class="contact__item">
          <svg class="contact__icon" viewBox="0 0 16 16" aria-hidden="true"><path d="M3 1.5l2.5 0 1.2 3.3-1.6 1.1a8 8 0 0 0 5 5l1.1-1.6 3.3 1.2v2.5c0 .6-.5 1.1-1.1 1.1A12.5 12.5 0 0 1 1.9 2.6C1.9 2 2.4 1.5 3 1.5z" fill="var(--ink-light)"/></svg>
          <span>(931) 555-0148</span>
        </li>
        <li class="contact__item">
          <svg class="contact__icon" viewBox="0 0 16 16" aria-hidden="true"><path d="M1 5c2-3 12-3 14 0l-2 2-2.5-1V4.5c-1.5-.5-3.5-.5-5 0V6L3 7z M3 9h10v5H3z" fill="var(--ink-light)"/></svg>
          <span>(629) 555-0173</span>
        </li>
        <li class="contact__item">
          <svg class="contact__icon" viewBox="0 0 16 16" aria-hidden="true"><rect x="1" y="3" width="14" height="10" fill="var(--ink-light)"/><path d="M1 3l7 6 7-6" fill="none" stroke="var(--brand-blue)" stroke-width="1.2"/></svg>
          <span>harborlineautoxq@mailnest.example</span>
        </li>
        <li class="contact__item">
          <svg class="contact__icon" viewBox="0 0 16 16" aria-hidden="true"><circle cx="8" cy="8" r="7" fill="var(--ink-light)"/><path d="M1 8h14M8 1c3 3 3 11 0 14M8 1c-3 3-3 11 0 14" fill="none" stroke="var(--brand-blue)" stroke-width="1"/></svg>
          <span>www.harborlineautoxq.net</span>
        </li>
      </ul>
    </div>
  </section>
</main>
</body>
</html>
```